Sprout & Shine General Card Design

Please see http://sprout-and-shine.example.org for more information about our program. In brief, we are a 501(c)(3) nonprofit organization that focuses on improving educational outcomes for all students through parent education and empowerment, K-12 curriculum development, K-12 staff development, learner-oriented live events, community service projects, and more. We are now preparing to launch our Sprout & Shine Educational Series, which is devoted to teaching children and the adults in their lives about making healthy food choices and regaining control over what is in their food by growing it themselves in easy, affordable self-watering container gardens that can be placed in spaces not otherwise suitable for growing fruits and vegetables, such as paved lots and rooftops, are portable, and can be quickly built from recycled materials. In fact, we have local businesses already lining up to donate clean, safe 5-gallon buckets for this initiative (our container design uses 5-gallon buckets). We have already built out content on the site to support as many of the Trail Ranger merit badges as we could tie to the instructional goals of our Sprout & Shine Educational Series. We are in the processes of developing K-12 curricula tied to the Common Core and STEM (science, technology, engineering, & math), which we will be giving away for free under a Creative Commons license to help public schools in states that have recently adopted the Common Core but can't afford to replace all their textbooks and don't have the time to scramble to create curricula of their own. This card will be used by all of our Sprout & Shine staff and volunteers to share out information about the program and promote it to others. It will go out in mailings, sit on display tables at events, be left at kiosks, and be handed out in person. It needs to be color-matched to our Sprout & Shine site. The logo on the site we created for our Sprout & Shine Educational Series was done using an online service and the quality of the image is quite poor (see attached file). When we use it in print materials and then convert them to PDF, the logo becomes pixelated. It's awful. We are not entirely married to keeping the logo if you can come up with something better and we are given the final JPG or PNG file of the logo to upload to the site so they match. If you can just improve the quality of the existing logo, that's fine, too. Please note that the phrase "Sprout & Shine Educational Series" is a service mark of Brightpath Families and should be followed by the letters "SM" in superscript at the end of the word "Series" in any logo you create.
Target Market(s)
parents of K-12 students, K-12 teachers, community service organizations, youth organizations, programs for the elderly, programs for the disabled
Industry/Entity Type
Community Service
Contact Information for Business Card
TMV4Families' Sprout & Shine Educational Series, http://sprout-and-shine.example.org, (555) 214-7390, Non-GMO/Organic Family & Community Gardening Workshops, K-12 Common Core/STEM Curricula Development, Community Service Projects, Online Gardening & Teaching Communities, Project-Based Learning Activities, Youth Leadership Projects, Fun Contests and Prizes, Corporate & Small Business Social Responsibility Programs, K-12 Staff Development, Education Research & Reporting

```html
<!DOCTYPE html>
<html lang="en">
<head>
<meta charset="utf-8">
<title>Sprout &amp; Shine Educational Series – Card Options</title>
<link rel="stylesheet" href="https://fonts.googleapis.com/css2?family=Merriweather:wght@700&family=Questrial&family=Didact+Gothic&family=Open+Sans:wght@400;700&display=swap">
<style>
  :root {
    --sheet: #ffffff;
    --label: #333333;
    --leaf-text: #4d8a1f;
    --leaf-dark: #2b5f10;
    --sage: #b3cd93;
    --band: #5b8a24;
    --ring: #8cbf2e;
    --sage-text: #5a7f1e;
    --body-text: #3c3c3c;
    --bullet: #ef8a12;
    --swoosh-orange: #f39a1e;
    --swoosh-yellow: #ffd23a;
    --ink: #1f2a10;
  }
  * { box-sizing: border-box; margin: 0; padding: 0; }
  html, body { width: 753px; height: 1200px; overflow: hidden; background: var(--sheet); }
  .sheet { position: relative; width: 753px; height: 1200px; border: 1px solid #e2e2e2; }
  .option-number { position: absolute; font: 400 36px "Open Sans", sans-serif; color: var(--label); }
  .card { position: absolute; overflow: hidden; box-shadow: 3px 4px 7px rgba(0,0,0,.35); }
  .card svg.card-art { position: absolute; inset: 0; }
  .card .layer { position: absolute; }

  /* Option 1 */
  .v-title { font-family: "Merriweather", serif; font-weight: 700; color: var(--leaf-text); line-height: 1; white-space: nowrap; }
  .v-title sup { font-size: 40%; vertical-align: top; position: relative; top: 2px; }
  .v-contact { font-family: "Open Sans", sans-serif; font-weight: 700; color: var(--leaf-dark); font-size: 13px; display: flex; align-items: center; gap: 3px; white-space: nowrap; }
  .brand-name { font-family: "Questrial", sans-serif; font-weight: 400; display: flex; align-items: center; gap: 6px; white-space: nowrap; }
  .brand-name .mark { width: 13px; height: 13px; border-radius: 50%; background: currentColor; }
  .v-list { list-style: none; font-family: "Questrial", sans-serif; font-size: 10.6px; line-height: 14.7px; color: var(--body-text); }
  .v-list li { position: relative; padding-left: 14px; }
  .v-list li::before { content: ""; position: absolute; left: 0; top: 4px; width: 6px; height: 6px; border-radius: 50%; background: var(--bullet); box-shadow: 0 0 0 1px #ffd27a inset; }
  .v-list li.cont::before { display: none; }

  /* Option 2 */
  .h-title { font-family: "Didact Gothic", sans-serif; color: var(--sage-text); line-height: 1; white-space: nowrap; }
  .h-title sup { font-size: 45%; vertical-align: top; }
  .h-contact { font-family: "Open Sans", sans-serif; font-weight: 700; color: var(--ink); font-size: 13.5px; display: flex; align-items: center; gap: 10px; white-space: nowrap; }
  .h-list { list-style: none; font-family: "Questrial", sans-serif; font-size: 11.2px; line-height: 16.2px; color: var(--body-text); white-space: nowrap; }
  .h-list li { position: relative; padding-left: 12px; }
  .h-list li::before { content: ""; position: absolute; left: 1px; top: 6px; width: 4px; height: 4px; border-radius: 50%; background: var(--ring); }
</style>
</head>
<body>
<div class="sheet">

  <div class="option-number" style="left:36px;top:70px;">1</div>

  <!-- Option 1: vertical front -->
  <div class="card card-v-front" style="left:82px;top:65px;width:262px;height:446px;">
    <svg class="card-art" width="262" height="446" viewBox="0 0 262 446">
      <defs>
        <radialGradient id="vGlow" cx=".5" cy=".48" r=".6">
          <stop offset="0" stop-color="#f3f9e2"/>
          <stop offset=".55" stop-color="#a9d454"/>
          <stop offset="1" stop-color="#5fa826"/>
        </radialGradient>
        <linearGradient id="beanLeaves" x1="0" y1="0" x2="1" y2="1">
          <stop offset="0" stop-color="#c9d8b0"/>
          <stop offset=".5" stop-color="#4f7a2a"/>
          <stop offset="1" stop-color="#2d4d18"/>
        </linearGradient>
        <linearGradient id="potPlants" x1="0" y1="0" x2="1" y2="1">
          <stop offset="0" stop-color="#7a4a30"/>
          <stop offset=".45" stop-color="#c0392b"/>
          <stop offset="1" stop-color="#3f6e22"/>
        </linearGradient>
      </defs>
      <rect width="262" height="446" fill="url(#vGlow)"/>
      <path role="img" aria-label="Photo of green bean plants climbing among leaves" d="M0 0H262V98Q140 108 0 126Z" fill="url(#beanLeaves)"/>
      <path d="M0 132Q140 114 262 102" fill="none" stroke="var(--swoosh-yellow)" stroke-width="3"/>
      <path d="M0 128Q140 110 262 98" fill="none" stroke="var(--swoosh-orange)" stroke-width="3"/>
      <path d="M0 292Q120 262 262 290" fill="none" stroke="var(--swoosh-orange)" stroke-width="4"/>
      <path d="M0 296Q120 266 262 294" fill="none" stroke="var(--swoosh-yellow)" stroke-width="2"/>
      <path role="img" aria-label="Photo of cucumber seedlings growing in red pots" d="M0 300Q120 270 262 298V446H0Z" fill="url(#potPlants)"/>
    </svg>
    <div class="layer v-title" style="left:26px;top:148px;font-size:26px;">Sprout &amp; Shine</div>
    <div class="layer v-title" style="left:26px;top:180px;font-size:20px;">Educational Series<sup>SM</sup></div>
    <div class="layer v-contact" style="left:40px;top:219px;">sprout-and-shine.example.org</div>
    <div class="layer v-contact" style="left:70px;top:244px;">
      <svg width="14" height="14" viewBox="0 0 24 24"><path d="M6.6 10.8a15.1 15.1 0 0 0 6.6 6.6l2.2-2.2a1 1 0 0 1 1-.25 11.4 11.4 0 0 0 3.6.57 1 1 0 0 1 1 1V20a1 1 0 0 1-1 1A17 17 0 0 1 3 4a1 1 0 0 1 1-1h3.5a1 1 0 0 1 1 1c0 1.25.2 2.45.57 3.6a1 1 0 0 1-.25 1Z" fill="var(--leaf-dark)"/></svg>
      (555) 214-7390
    </div>
    <div class="layer brand-name" style="left:14px;top:410px;font-size:15px;color:#e8f4cc;"><span class="mark"></span>Brightpath Families</div>
  </div>

  <!-- Option 1: vertical back -->
  <div class="card card-v-back" style="left:408px;top:67px;width:262px;height:444px;">
    <svg class="card-art" width="262" height="444" viewBox="0 0 262 444">
      <defs>
        <radialGradient id="vGlowBack" cx=".5" cy=".4" r=".65">
          <stop offset="0" stop-color="#f3f9e2"/>
          <stop offset=".6" stop-color="#a9d454"/>
          <stop offset="1" stop-color="#5fa826"/>
        </radialGradient>
        <linearGradient id="pansyPot" x1="0" y1="0" x2="1" y2="1">
          <stop offset="0" stop-color="#3d5e2a"/>
          <stop offset=".4" stop-color="#5a3d7a"/>
          <stop offset=".7" stop-color="#b48a6e"/>
          <stop offset="1" stop-color="#2f4f20"/>
        </linearGradient>
      </defs>
      <rect width="262" height="444" fill="url(#vGlowBack)"/>
      <path d="M0 336Q150 268 262 320" fill="none" stroke="var(--swoosh-orange)" stroke-width="4"/>
      <path d="M0 340Q150 272 262 324" fill="none" stroke="var(--swoosh-yellow)" stroke-width="2"/>
      <path role="img" aria-label="Photo of purple and cream pansies in a clay pot" d="M0 344Q150 276 262 328V444H0Z" fill="url(#pansyPot)"/>
    </svg>
    <div class="layer v-title" style="left:37px;top:18px;font-size:22px;">Sprout &amp; Shine</div>
    <div class="layer v-title" style="left:37px;top:46px;font-size:18px;">Educational Series<sup>SM</sup></div>
    <ul class="layer v-list" style="left:22px;top:82px;width:240px;">
      <li>Non-GMO/Organic Family &amp; Community<br>Gardening Workshops;</li>
      <li>K-12 Common Core/STEM Curricula<br>Development;</li>
      <li>Community Service Projects;</li>
      <li>Online Gardening &amp; Teaching<br>Communities;</li>
      <li>Project-Based Learning Activities;</li>
      <li>Youth Leadership Projects;</li>
      <li>Fun Contests and Prizes;</li>
      <li>Corporate &amp; Small Business Social<br>Responsibility Programs;</li>
      <li>K-12 Staff Development</li>
      <li class="cont">Education Research &amp; Reporting.</li>
    </ul>
  </div>

  <div class="option-number" style="left:38px;top:575px;">2</div>

  <!-- Option 2: horizontal front -->
  <div class="card card-h-front" style="left:84px;top:565px;width:444px;height:267px;">
    <svg class="card-art" width="444" height="267" viewBox="0 0 444 267">
      <defs>
        <linearGradient id="cucumberVines" x1="0" y1="0" x2="1" y2="1">
          <stop offset="0" stop-color="#9aa88a"/>
          <stop offset=".5" stop-color="#2f6a1c"/>
          <stop offset="1" stop-color="#8a3a22"/>
        </linearGradient>
        <clipPath id="frontArc"><rect x="0" y="14" width="444" height="253"/></clipPath>
      </defs>
      <rect width="444" height="267" fill="var(--sage)"/>
      <rect width="444" height="14" fill="var(--band)"/>
      <g clip-path="url(#frontArc)">
        <circle cx="468" cy="300" r="236" fill="var(--ring)"/>
        <circle role="img" aria-label="Photo of cucumber vines with yellow flowers in pots" cx="468" cy="300" r="228" fill="url(#cucumberVines)"/>
      </g>
    </svg>
    <div class="layer h-title" style="left:28px;top:28px;font-size:35px;">Sprout &amp; Shine</div>
    <div class="layer h-title" style="left:28px;top:68px;font-size:25px;">Educational Series<sup>SM</sup></div>
    <div class="layer h-contact" style="left:32px;top:156px;">
      <svg width="15" height="15" viewBox="0 0 24 24" fill="none" stroke="var(--ink)" stroke-width="2"><circle cx="12" cy="12" r="10"/><ellipse cx="12" cy="12" rx="4.5" ry="10"/><path d="M2 12h20M4 7h16M4 17h16"/></svg>
      sprout-and-shine.example.org
    </div>
    <div class="layer h-contact" style="left:32px;top:185px;">
      <svg width="15" height="15" viewBox="0 0 24 24"><path d="M6.6 10.8a15.1 15.1 0 0 0 6.6 6.6l2.2-2.2a1 1 0 0 1 1-.25 11.4 11.4 0 0 0 3.6.57 1 1 0 0 1 1 1V20a1 1 0 0 1-1 1A17 17 0 0 1 3 4a1 1 0 0 1 1-1h3.5a1 1 0 0 1 1 1c0 1.25.2 2.45.57 3.6a1 1 0 0 1-.25 1Z" fill="var(--ink)"/></svg>
      (555) 214-7390
    </div>
    <div class="layer brand-name" style="left:32px;top:228px;font-size:17px;color:var(--leaf-dark);"><span class="mark"></span>Brightpath Families</div>
  </div>

  <!-- Option 2: horizontal back -->
  <div class="card card-h-back" style="left:85px;top:867px;width:444px;height:264px;">
    <svg class="card-art" width="444" height="264" viewBox="0 0 444 264">
      <defs>
        <linearGradient id="pansyPotWide" x1="0" y1="0" x2="1" y2="1">
          <stop offset="0" stop-color="#6a4a8a"/>
          <stop offset=".4" stop-color="#c49a78"/>
          <stop offset=".7" stop-color="#3e6a2a"/>
          <stop offset="1" stop-color="#4a3a6e"/>
        </linearGradient>
        <clipPath id="backArc"><rect x="0" y="14" width="444" height="250"/></clipPath>
      </defs>
      <rect width="444" height="264" fill="var(--sage)"/>
      <rect width="444" height="14" fill="var(--band)"/>
      <g clip-path="url(#backArc)">
        <circle cx="498" cy="330" r="244" fill="var(--ring)"/>
        <circle role="img" aria-label="Photo of purple and cream pansies in a clay pot" cx="498" cy="330" r="236" fill="url(#pansyPotWide)"/>
      </g>
    </svg>
    <div class="layer h-title" style="left:30px;top:32px;font-size:21px;">Sprout &amp; Shine Educational Series<sup>SM</sup></div>
    <ul class="layer h-list" style="left:32px;top:68px;width:380px;">
      <li>Non-GMO/Organic Family &amp; Community Gardening Workshops</li>
      <li>K-12 Common Core/STEM Curricula Development</li>
      <li>Community Service Projects</li>
      <li>Online Gardening &amp; Teaching Communities</li>
      <li>Project-Based Learning Activities</li>
      <li>Youth Leadership Projects</li>
      <li>Fun Contests and Prizes</li>
      <li>Corporate &amp; Small Business Social<br>Responsibility Programs</li>
      <li>K-12 Staff Development</li>
      <li>Education Research &amp; Reporting</li>
    </ul>
  </div>

</div>
</body>
</html>
```